Business card for law firm

Need business card for new law firm. Think confident, authoritative, conservative, but not stuffy or old-fashioned.

Contact Information for Business Card

Content for card - logo (uploaded), plus the following:

Paul Whitcombe (larger font)
Managing Partner (larger font, but not as large as name)
Level 9, 7 Ferris Lane
Sydney NSW 2000
Main Tel 02 9364 2710
Direct Tel 02 8472 3159
Email paul@qvlegal.com.au
www.qvlegal.com.au

Letterhead design should include logo plus:
Level 9, 7 Ferris Lane
Sydney NSW 2000
Tel 02 8472 3159
www.qvlegal.com.au

```html
<!DOCTYPE html>
<html lang="en">
<head>
<meta charset="UTF-8">
<title>Quayvale Legal – Business Card</title>
<link href="https://fonts.googleapis.com/css2?family=Jost:wght@400;500;700&display=swap" rel="stylesheet">
<style>
  :root {
    --navy: #0d1f5c;
    --navy-deep: #0a1a4f;
    --ink: #1a1a1a;
    --text-grey: #2b2b2b;
    --white: #ffffff;
    --backdrop: #5a5a5c;
  }
  html, body {
    margin: 0;
    padding: 0;
    width: 1200px;
    height: 1000px;
    overflow: hidden;
    background: var(--backdrop);
    font-family: 'Jost', sans-serif;
  }
  .canvas {
    position: relative;
    width: 1200px;
    height: 1000px;
  }
  .card {
    position: absolute;
    width: 700px;
    height: 400px;
    border-radius: 24px;
    overflow: hidden;
    box-shadow: 0 18px 40px rgba(0,0,0,0.35);
  }

  /* Front: navy */
  .card-front {
    left: 430px;
    top: 60px;
    background: var(--navy);
    color: var(--white);
  }
  .card-front .brand {
    position: absolute;
    left: 0; right: 0;
    top: 140px;
    display: flex;
    justify-content: center;
    align-items: center;
    gap: 18px;
  }
  .brand-square {
    width: 44px;
    height: 44px;
    background: currentColor;
  }
  .brand-name {
    font-weight: 500;
    font-size: 46px;
    letter-spacing: 3px;
    text-transform: uppercase;
    line-height: 1;
  }
  .card-front .web {
    position: absolute;
    left: 0; right: 0;
    top: 300px;
    text-align: center;
    font-size: 18px;
    font-weight: 500;
    letter-spacing: 0.5px;
  }

  /* Back: white */
  .card-back {
    left: 70px;
    top: 520px;
    background: var(--white);
    color: var(--text-grey);
  }
  .contact {
    position: absolute;
    left: 56px;
    top: 70px;
    font-size: 17px;
    line-height: 1.3;
  }
  .contact .person {
    font-weight: 700;
    font-size: 24px;
    color: var(--navy);
    text-transform: uppercase;
    margin: 0;
    line-height: 1.1;
  }
  .contact .role {
    margin: 0 0 26px;
    font-size: 17px;
  }
  .contact .address {
    margin: 0 0 20px;
  }
  .contact .label {
    font-weight: 700;
    color: var(--navy);
  }
  .contact .line { margin: 0; display: flex; align-items: center; gap: 6px; }
  .mail-icon { width: 16px; height: 12px; }

  .card-back .brand {
    position: absolute;
    right: 60px;
    top: 150px;
    display: flex;
    align-items: center;
    gap: 14px;
    color: var(--ink);
  }
  .card-back .brand-square {
    width: 36px; height: 36px;
    background: var(--navy);
  }
  .card-back .brand-name {
    font-size: 36px;
    color: var(--ink);
  }
  .band {
    position: absolute;
    left: 0; bottom: 0;
    width: 700px;
    height: 70px;
  }
  .band-web {
    position: absolute;
    right: 70px;
    bottom: 22px;
    color: var(--white);
    font-size: 19px;
    font-weight: 500;
    letter-spacing: 0.5px;
  }
</style>
</head>
<body>
<div class="canvas">

  <section class="card card-front">
    <div class="brand">
      <span class="brand-square"></span>
      <span class="brand-name">Quayvale Legal</span>
    </div>
    <div class="web">www.qvlegal.com.au</div>
  </section>

  <section class="card card-back">
    <div class="contact">
      <p class="person">Paul Whitcombe</p>
      <p class="role">Managing Partner</p>
      <p class="address">Level 9, 7 Ferris Lane<br>Sydney NSW 2000</p>
      <p class="line"><span class="label">Main Tel</span> 02 9364 2710</p>
      <p class="line"><span class="label">Direct Tel</span> 02 8472 3159</p>
      <p class="line">
        <svg class="mail-icon" viewBox="0 0 16 12" aria-hidden="true">
          <rect x="0.5" y="0.5" width="15" height="11" fill="var(--navy)"/>
          <polyline points="1,1 8,7 15,1" fill="none" stroke="#fff" stroke-width="1.2"/>
        </svg>
        paul@qvlegal.com.au
      </p>
    </div>

    <div class="brand">
      <span class="brand-square"></span>
      <span class="brand-name">Quayvale Legal</span>
    </div>

    <svg class="band" viewBox="0 0 700 70" aria-hidden="true">
      <polygon points="420,12 700,12 700,70 360,70" fill="var(--navy)"/>
    </svg>
    <div class="band-web">www.qvlegal.com.au</div>
  </section>

</div>
</body>
</html>
```